Book Cover on Entrepreneurship for Eye Doctors

Book Title: The Lens Practice Builder: How to launch with confidence
Author: Rufus Tembley, Optom, MBA, DBA, EIC
I need a Book Cover with the following descriptions:
Topic: the book topic is entrepreneurship knowledge for eye care professionals.
The book's audience: eye care professionals who you know as Opticians, who sell eyeglasses and sunglasses;
Optometrists, test eyes, fit contact lenses, and prescribe medication
Ophthalmologists, perform eye surgery
More about the audience:
1- Young eye care professionals who don’t know about entrepreneurship and those who are stuck in the 9-to-5 job;
2- This is the first book written on entrepreneurship with eye care professionals in mind.
3- Private practice owners the established business guys who are looking to grow their business;
4- Many eye care professionals are MBA holders they may have learned a little bit about entrepreneurship during their MBA studies.
Use the sample cover above and the suggestions that follow as a guide:
1- The cover should be very simple leaving an empty space somewhere to sign the book;
2- The Title and author name should use a modern font;
3- The cover should provide info about what's inside the book through illustrations, for example:
a- Gears: illustrating entrepreneur growth mindset (or anything more explicit)
b- Spectacles, sunglasses, lenses, eye drops, or any other eye care-related correction tools illustrating eye care (or anything more explicit)
c- Symbols illustrating ideas, opportunity, and profit, like money, charts, light bulbs, brain, and coins,...(or anything more explicit)
d- Entrepreneurship illustrated by Briefcase, tie, suit,... (or anything more explicit)

The rest is your creativity and imagination interplay.

Target Market(s)

Eye care professionals: Opticians, Optometrists, Ophthalmologists, Eye Care Administrators, Students in eye specialties.

Industry/Entity Type

eye care

Requirements
Must have
• 1- The cover should be very simple leaving an empty space somewhere to sign the book; 2- The Title and author name should use a modern font; 3- The cover should provide info about what's inside the book through illustrations, for example: a- Gears: illustrating entrepreneur growth mindset (or anything more explicit) b- Spectacles, sunglasses, lenses, eye drops, or any other eye care-related correction tools illustrating eye care (or anything more explicit) c- Symbols illustrating ideas, opportunity, and profit, like money, charts, light bulbs, brain, and coins,...(or anything more explicit) d- Entrepreneurship illustrated by Briefcase, tie, suit,... (or anything more explicit)

```html
<!DOCTYPE html>
<html lang="en">
<head>
<meta charset="utf-8">
<title>The Lens Practice Builder – Cover Spread</title>
<link href="https://fonts.googleapis.com/css2?family=Bebas+Neue&family=Montserrat:wght@400;500&display=swap" rel="stylesheet">
<style>
  :root {
    --navy: #0c2440;
    --cyan: #0ea8cc;
    --paper: #e7f2f2;
    --slate: #94a4ad;
    --white: #ffffff;
  }
  * { margin: 0; padding: 0; box-sizing: border-box; }
  html, body { width: 1200px; height: 968px; overflow: hidden; background: var(--white); }
  .spread { position: relative; width: 1200px; height: 968px; }

  .panel { position: absolute; top: 121px; height: 725px; background: var(--paper); }
  .back-cover { left: 76px; width: 483px; }
  .spine { left: 559px; width: 80px; background: var(--navy); }
  .front-cover { left: 639px; width: 484px; }

  .base-band { position: absolute; left: 0; right: 0; bottom: 0; height: 62px; background: var(--navy); }

  .hero-photo {
    position: absolute; left: 0; top: 0; width: 100%; height: 290px;
    background:
      radial-gradient(ellipse at 50% 70%, rgba(110,200,235,.55), transparent 60%),
      linear-gradient(180deg, #b9b2ac 0%, #3b5a78 30%, #4f7fa8 60%, #a7d4e4 85%, var(--paper) 100%);
  }

  .blurb {
    position: absolute; font-family: "Montserrat", sans-serif; font-size: 10px;
    line-height: 12.1px; color: var(--navy); text-align: justify;
  }
  .blurb-main { left: 35px; top: 211px; width: 413px; }
  .blurb-bio { left: 162px; top: 461px; width: 286px; }

  .author-photo { position: absolute; left: 36px; top: 460px; width: 117px; height: 152px; background: var(--slate); }

  .back-author {
    position: absolute; left: 0; width: 100%; top: 423px; text-align: center; white-space: nowrap;
    font-family: "Bebas Neue", sans-serif; font-size: 16px; line-height: 20px; letter-spacing: 2.6px; color: var(--navy);
  }

  .front-author {
    position: absolute; left: 0; width: 100%; bottom: 14px; text-align: center; white-space: nowrap;
    font-family: "Bebas Neue", sans-serif; font-size: 30px; letter-spacing: 1.4px; color: var(--white);
  }

  .title-layer { position: absolute; left: 0; top: 0; width: 1200px; height: 968px; }
  .title-layer text { font-family: "Bebas Neue", sans-serif; }
  .ink-navy { fill: var(--navy); }
  .ink-cyan { fill: var(--cyan); }
  .ink-white { fill: var(--white); }
  .tagline-rule { stroke: url(#rule-fade); stroke-width: 1.2; }
</style>
</head>
<body>
<div class="spread">

  <section class="panel back-cover">
    <p class="blurb blurb-main">
      Lorem ipsum dolor sit amet, consectetuer adipiscing elit, sed diam nonummy nibh euismod tincidunt ut laoreet dolore magna aliquam erat volutpat. Ut wisi enim ad minim veniam, quis nostrud exerci tation ullamcorper suscipit lobortis nisl ut aliquip ex ea commodo consequat. Duis autem vel eum iriure dolor in hendrerit in vulputate velit esse molestie consequat, vel illum dolore eu feugiat nulla facilisis at vero eros et accumsan et iusto odio dignissim qui blandit praesent luptatum zzril delenit augue duis dolore te feugait nulla facilisi.<br>
      Lorem ipsum dolor sit amet, cons ectetuer adipiscing elit, sed diam nonummy nibh euismod tincidunt ut laoreet dolore magna aliquam erat volutpat. Ut wisi enim ad minim veniam, quis nostrud exerci tation ullamcorper suscipit lobortis nisl ut aliquip ex ea commodo consequat.<br>
      Lorem ipsum dolor sit amet, consectetuer adipiscing elit, sed diam nonummy nibh euismod tincidunt ut laoreet dolore magna aliquam erat volutpat. Ut wisi enim ad minim veniam, quis nostrud exerci tation ullamcorper suscipit lobortis nisl ut aliquip ex ea commodo consequat. Duis autem vel eum iriure dolor in hendrerit in vulputate velit esse molestie consequat.
    </p>
    <p class="back-author">Rufus Tembley, Optom, MBA, DBA, EIC</p>
    <div class="author-photo" role="img" aria-label="Author portrait placeholder"></div>
    <p class="blurb blurb-bio">
      Lorem ipsum dolor sit amet, consectetuer adipiscing elit, sed diam nonummy nibh euismod tincidunt ut laoreet dolore magna aliquam erat volutpat. Ut wisi enim ad minim veniam, quis nostrud exerci tation ullamcorper suscipit lobortis nisl ut aliquip ex ea commodo consequat. Duis autem vel eum iriure dolor in hendrerit in vulputate velit esse molestie consequat, vel illum dolore eu feugiat nulla facilisis at vero eros et accumsan et iusto odio dignissim qui blandit praesent luptatum zzril delenit augue duis dolore te feugait nulla facilisi.<br>
      Lorem ipsum dolor sit amet, cons ectetuer adipiscing elit, sed diam nonummy nibh euismod tincidunt ut laoreet dolore magna aliquam erat volutpat.
    </p>
    <div class="base-band"></div>
  </section>

  <section class="panel spine"></section>

  <section class="panel front-cover">
    <div class="hero-photo" role="img" aria-label="Photo of hands at a desk with a glowing business dashboard of bar and line charts, gears, spectacles, an eye, a briefcase and a pie chart"></div>
    <div class="base-band"></div>
    <p class="front-author">Rufus Tembley, Optom, MBA, DBA, EIC</p>
  </section>

  <svg class="title-layer" viewBox="0 0 1200 968" aria-label="Book title">
    <defs>
      <linearGradient id="rule-fade" x1="0" x2="1" y1="0" y2="0">
        <stop offset="0" stop-color="#0ea8cc" stop-opacity="0"/>
        <stop offset="0.15" stop-color="#0ea8cc"/>
        <stop offset="0.85" stop-color="#0ea8cc"/>
        <stop offset="1" stop-color="#0ea8cc" stop-opacity="0"/>
      </linearGradient>
    </defs>
    <g class="back-title">
      <text class="ink-navy" x="214" y="213" font-size="86" textLength="207" lengthAdjust="spacingAndGlyphs">THE LENS</text>
      <text class="ink-navy" x="221" y="274" font-size="82" textLength="200" lengthAdjust="spacingAndGlyphs">PRACTICE</text>
      <text class="ink-cyan" x="221" y="309" font-size="44" textLength="201" lengthAdjust="spacingAndGlyphs">BUILDER</text>
    </g>
    <g class="spine-text">
      <text transform="translate(609 767) rotate(-90)" font-size="31" textLength="290" lengthAdjust="spacingAndGlyphs"><tspan class="ink-white">THE LENS PRACTICE </tspan><tspan class="ink-cyan">BUILDER</tspan></text>
      <text class="ink-white" transform="translate(606 458) rotate(-90)" font-size="20" letter-spacing="1.5" textLength="295" lengthAdjust="spacingAndGlyphs">RUFUS TEMBLEY, OPTOM, MBA, DBA, EIC</text>
    </g>
    <g class="front-title">
      <text class="ink-navy" x="673" y="524" font-size="155" textLength="394" lengthAdjust="spacingAndGlyphs">THE LENS</text>
      <text class="ink-navy" x="680" y="644" font-size="160" textLength="390" lengthAdjust="spacingAndGlyphs">PRACTICE</text>
      <text class="ink-cyan" x="689" y="710" font-size="82" textLength="382" lengthAdjust="spacingAndGlyphs">BUILDER</text>
    </g>
    <g class="tagline">
      <line class="tagline-rule" x1="745" y1="731" x2="1023" y2="731"/>
      <text class="ink-navy" x="884" y="755" font-size="22" text-anchor="middle" textLength="262" lengthAdjust="spacingAndGlyphs">HOW TO LAUNCH WITH CONFIDENCE</text>
      <line class="tagline-rule" x1="745" y1="762" x2="1023" y2="762"/>
    </g>
  </svg>

</div>
</body>
</html>
```